Wordpress Design For Financial Investment Company

//** NEW WIREFRAME ADDED TO HELP WITH LAYOUT ISSUES. PLEASE REFER TO WIREFRAME IN ATTACHED FILES. NO DESIGN WILL BE CONSIDERED IF IT DOES NOT FOLLOW THE WIREFRAME. **//
//** PLEASE READ THE ENTIRE BRIEF INCLUDING ALL UPDATES TO THE BRIEF. THE CLIENT IS VERY SPECIFIC ABOUT WHAT THEY WANT AND I'VE COVERED SEVERAL THINGS IN THE UPDATES. THERE IS ALSO A VIDEO UPDATE THAT HAS SOME VALUABLE INFORMATION IN IT FOR THIS CONTEST. **//
The client is an investment advisor who needs a new website designed. The current site is http://www.velmorhold.example.
The client wants the site to be green to match the attached logo.
The home page should have relevant images in the rotator. No people hugging! This is a financial investment site, not a family counseling site.
Also, the client wants 4 buttons on the home page to highlight the 4 main areas they focus on:
Investment Advice and Education
General Financial Planning
Retirement Planning
401K Planning
The top right area of the site needs to have their phone number, a call to action, and 2 buttons.
Their phone number is 303-418-7719
The call to action should say something like "Call for a free consultation!"
The buttons need to say:
Login To Your Brokavell Account
Login To Your Quillbrook Account
The final design should communicate professionalism, financial safety and growth.
Main navigation should be:
Home
About Us
Associates
Services
Contact
Mission Statement (Could also be "Our Mission")
This is a site that the client likes: http://www.pkwadvisoryfirm.example/
Updates
The designs should not have:
Newsletter content. A newsletter sign up is fine
Learning Center
Calculators
Stock prices/tickers
The design should have a contact form on the page.
I have talked to my client and have some updates. I did a video update because I thought it would be easier to show what I'm trying to get across.
Reason: I am going to be extending the contest a few more days. I'm still not getting quite what I want and very few people are even trying to follow the creative brief and the updates to it.
PLEASE read the entire brief and the updates. There is also a video I made that explains everything. I've also attached a wireframe.
Thanks!
Target Market(s)
People looking for a high-end financial investment company.
Industry/Entity Type
Investment
Requirements
Must have
- !!FOLLOW THE WIREFRAME FOR LAYOUT!!
!!THEIR LOGO!!
4 buttons to highlight their main practice areas
Phone number in the top right
"Free Consultation" call to action
2 Login buttons in the top right
A contact form on the page.
Should not have
- The designs should not have:
Learning Center
Calculators
Stock prices/tickers

```html
<!DOCTYPE html>
<html lang="en">
<head>
<meta charset="utf-8">
<title>Velmor Holdings – Financial Consultant</title>
<link href="https://fonts.googleapis.com/css2?family=Arimo:wght@400;700&family=Lora:ital@1&display=swap" rel="stylesheet">
<style>
:root{
  --green-dark:#1f3a2b;
  --green-deep:#17291f;
  --green-mid:#2c4a38;
  --green-band:#3b5c48;
  --green-bright:#3f9a4f;
  --green-link:#6fbf7a;
  --beige:#f1e5d3;
  --beige-light:#fbf1e4;
  --card:#f4e9da;
  --ink:#2b2b2b;
  --muted:#7a7366;
  --line:#c9b9a0;
  --white:#fff;
}
*{box-sizing:border-box;margin:0;padding:0}
html,body{width:690px;height:1200px;overflow:hidden}
body{font-family:"Arimo",sans-serif;background:var(--beige);color:var(--ink);position:relative}
.abs{position:absolute}
.header{left:0;top:0;width:690px;height:270px;background:var(--green-dark)}
.login{top:19px;width:89px;height:20px;border:1px solid #8fae98;border-radius:3px;background:var(--green-mid);color:var(--white);font-size:7px;line-height:8px;padding:2px 4px 0 22px}
.login svg{position:absolute;left:6px;top:4px}
.nav{left:0;top:57px;width:690px;height:34px;background:linear-gradient(#4a6b55,#2f4d3a)}
.nav a{position:absolute;top:12px;color:var(--white);font-size:9px;text-decoration:none}
.nav .home{left:9px;top:3px;width:72px;height:28px;background:var(--green-deep);text-align:center;line-height:28px}
.brand{left:287px;top:38px;width:98px;height:98px;border-radius:50%;background:var(--beige);border:4px solid var(--green-deep);display:flex;align-items:center;justify-content:center;text-align:center;font-size:13px;font-weight:700;color:var(--green-deep);line-height:15px}
.tagline{left:214px;top:102px;width:250px;height:25px}
.tagline span{position:absolute;left:0;top:7px;width:250px;text-align:center;font-family:"Lora",serif;font-style:italic;font-size:7px;color:var(--ink)}
.call{left:492px;top:106px;color:var(--white);font-size:9.5px;display:flex;align-items:center;gap:5px}
.call i{display:block;width:20px;height:14px;border-radius:7px;background:var(--green-bright)}
.slider{left:8px;top:138px;width:670px;height:192px;background:var(--beige-light);border:1px solid var(--line);border-radius:4px;box-shadow:0 1px 3px rgba(0,0,0,.3)}
.slide-photo{left:10px;top:7px;width:435px;height:176px;background:linear-gradient(#5d94c8 0%,#a9cbe4 55%,#d9a866 62%,#c98f4a 100%)}
.slide-title{left:472px;top:5px;font-size:16px;color:var(--green-mid);letter-spacing:.3px}
.slide-text{left:472px;top:44px;width:188px;font-size:6.6px;line-height:9.6px;text-align:justify}
.btn{display:block;text-align:center;font-size:7px;border-radius:2px}
.btn-light{background:var(--beige-light);border:1px solid #b8a98f;color:var(--ink)}
.btn-dark{background:var(--green-mid);color:var(--white)}
.dots{left:610px;top:177px;display:flex;gap:4px}
.dots b{width:10px;height:10px;border-radius:50%;background:#bdb6aa}
.dots b:first-child{background:var(--green-mid)}
.area{left:9px;width:198px;height:43px;background:var(--green-mid);border:1px solid var(--green-deep);color:#7cc48a;font-size:10px;line-height:11px;padding:12px 0 0 67px;text-transform:uppercase}
.area.active{background:linear-gradient(#4aa65a,#2f7f3c);color:var(--green-deep)}
.area i{position:absolute;left:12px;top:8px;width:34px;height:26px;border-radius:3px;background:var(--green-deep)}
.area i::after{content:"";position:absolute;left:9px;top:5px;width:16px;height:16px;border-radius:3px;background:#c9a24a}
.section-title{font-size:9.5px;color:var(--muted);text-transform:uppercase;letter-spacing:.3px}
.card{width:197px;height:159px;border:1px solid var(--line);border-radius:3px;background:var(--card)}
.card h3{height:16px;background:var(--green-mid);color:var(--white);font-size:9px;font-weight:400;text-align:center;line-height:16px;border-radius:3px 3px 0 0}
.card .photo{position:absolute;left:5px;top:26px;width:185px;height:60px}
.card p{position:absolute;left:5px;top:94px;width:186px;font-size:6.6px;line-height:9.6px;text-align:justify}
.card .btn{position:absolute;left:66px;top:150px;width:62px;height:13px;line-height:12px}
.body-text{font-size:6.6px;line-height:9.6px}
.news-date{left:9px;width:39px;height:27px;border-radius:3px;background:var(--green-mid);color:var(--white);text-align:center;font-size:13px;font-weight:700;line-height:13px;padding-top:2px}
.news-date small{display:block;font-size:7px;font-weight:400}
.more{font-size:6.6px;font-style:italic;text-decoration:underline;color:var(--ink)}
.contact{left:436px;top:763px;width:241px;height:206px;background:var(--beige-light)}
.contact label{position:absolute;left:15px;font-size:6.6px}
.contact .field{position:absolute;left:77px;width:148px;height:15px;border:1px solid #9a9282;background:var(--beige-light)}
.footer{left:0;top:1028px;width:690px;height:150px;background:var(--green-deep);color:var(--white)}
.footer h4{position:absolute;top:11px;font-size:10px;font-weight:400;letter-spacing:.3px}
.footer ul{position:absolute;top:31px;list-style:none;font-size:7px;line-height:8.8px;color:var(--green-link)}
.copyright{left:0;top:1177px;width:690px;height:23px;background:#111c15;color:#ddd;font-size:7px;text-align:center;line-height:14px}
</style>
</head>
<body>

<header class="abs header">
  <a class="abs login" style="left:492px"><svg width="10" height="10" viewBox="0 0 10 10"><rect x="1" y="4" width="8" height="6" fill="#d9b23c"/><path d="M3 4V2.5a2 2 0 0 1 4 0V4" stroke="#d9b23c" fill="none"/></svg>Login for your<br>Brokavell account</a>
  <a class="abs login" style="left:587px"><svg width="10" height="10" viewBox="0 0 10 10"><rect x="1" y="4" width="8" height="6" fill="#d9b23c"/><path d="M3 4V2.5a2 2 0 0 1 4 0V4" stroke="#d9b23c" fill="none"/></svg>Login for your<br>Quillbrook account</a>
  <nav class="abs nav">
    <a class="home">Home</a>
    <a style="left:108px">About us</a>
    <a style="left:193px">Associate</a>
    <a style="left:425px">Services</a>
    <a style="left:509px">Our Mission</a>
    <a style="left:607px">Contact us</a>
  </nav>
  <div class="abs brand">Velmor<br>Holdings</div>
  <div class="abs tagline">
    <svg width="250" height="25" viewBox="0 0 250 25"><path d="M0 1H250L238 12.5 250 24H0L12 12.5Z" fill="#efe3cf"/></svg>
    <span>"always do right. this gratify some people &amp; astonish the rest."</span>
  </div>
  <div class="abs call"><i></i>Call us for free Consultation : 303-418-7719</div>
</header>

<section class="abs slider">
  <div class="abs slide-photo" role="img" aria-label="Hand placing a coin into a white piggy bank on a sandy beach under blue sky"></div>
  <h2 class="abs slide-title">RETIREMENT PLAN</h2>
  <p class="abs slide-text">Lorem Ipsum is simply dummy text of the printing and typesetting industry. Lorem Ipsum has been the industry's standard dummy text ever since the 1500s, when an unknown printer took a galley of type and scrambled it to make a type specimen book. It has survived not only five centuries, but also the leap into electronic typesetting, remaining essentially unchanged. It was popularised in the 1960s with the release of Letraset sheets containing Lorem Ipsum passages, and more recently with desktop publish-</p>
  <a class="abs btn btn-light" style="left:471px;top:150px;width:61px;height:14px;line-height:13px">Learn more</a>
  <div class="abs dots"><b></b><b></b><b></b><b></b></div>
</section>

<a class="abs area" style="top:364px"><i></i>Investment advice<br>and education</a>
<a class="abs area active" style="top:411px"><i></i>General financial<br>planning</a>
<a class="abs area" style="top:460px"><i></i>Retirement<br>plan</a>
<a class="abs area" style="top:509px"><i></i>401 K<br>planing</a>

<h3 class="abs section-title" style="left:9px;top:586px">Latest Event</h3>
<div class="abs" role="img" aria-label="Business people applauding at a meeting" style="left:9px;top:609px;width:108px;height:36px;background:linear-gradient(90deg,#a9bfd3,#dfe6ec)"></div>
<p class="abs body-text" style="left:9px;top:659px;width:200px">Lorem Ipsum is simply dummy text of the printing and typeset-ting industry. Lorem Ipsum has been the industry's standard dummy text ever since the 1500s, when an unknown printer took a galley of type and scrambled it to make a type specimen</p>
<a class="abs body-text" style="left:9px;top:704px;font-weight:700;text-decoration:underline">Read more</a>

<article class="abs card" style="left:262px;top:364px">
  <h3>ABOUT US</h3>
  <div class="photo" role="img" aria-label="Young businessman in a suit adjusting his glasses" style="background:linear-gradient(90deg,#9a9ea3,#e3e4e6)"></div>
  <p>Lorem Ipsum is simply dummy text of the printing and typesetting industry. Lorem Ipsum has been the industry's standard dummy text ever since the 1500s, when an unknown printer took a galley of type and scrambled it to make a type specimen book. It has survived not only five</p>
  <a class="btn btn-dark">Learn more</a>
</article>
<article class="abs card" style="left:480px;top:364px">
  <h3>WHY CUSTOMER CHOSE US</h3>
  <div class="photo" role="img" aria-label="Smiling group of business colleagues" style="background:linear-gradient(90deg,#bcd3e8,#eef3f7)"></div>
  <p>Lorem Ipsum is simply dummy text of the printing and typesetting industry. Lorem Ipsum has been the industry's standard dummy text ever since the 1500s, when an unknown printer took a galley of type and scrambled it to make a type specimen book. It has survived not only five</p>
  <a class="btn btn-light">Learn more</a>
</article>
<article class="abs card" style="left:262px;top:546px">
  <h3>OUR MISSION</h3>
  <div class="photo" role="img" aria-label="Smiling businessman in front of his team" style="background:linear-gradient(90deg,#b9cbe0,#e9e3da)"></div>
  <p>Lorem Ipsum is simply dummy text of the printing and typesetting industry. Lorem Ipsum has been the industry's standard dummy text ever since the 1500s, when an unknown printer took a galley of type and scrambled it to make a type specimen book. It has survived not only five</p>
  <a class="btn btn-light">Learn more</a>
</article>
<article class="abs card" style="left:480px;top:546px">
  <h3>SUPPPORT</h3>
  <div class="photo" role="img" aria-label="Smiling support representative" style="background:linear-gradient(90deg,#ece6df,#d8c1ad)"></div>
  <p>Lorem Ipsum is simply dummy text of the printing and typesetting industry. Lorem Ipsum has been the industry's standard dummy text ever since the 1500s, when an unknown printer took a galley of type and scrambled it to make a type specimen book. It has survived not only five</p>
  <a class="btn btn-light">Learn more</a>
</article>

<div class="abs" style="left:0;top:738px;width:690px;border-top:1px dashed #8f9a8c"></div>

<h3 class="abs section-title" style="left:9px;top:763px;color:var(--green-mid)">Latest News</h3>
<div class="abs" style="left:100px;top:760px;width:24px;height:16px;background:#c9ccc8;border-radius:2px;transform:rotate(-12deg)"></div>
<div class="abs news-date" style="top:787px">28<small>Feb</small></div>
<p class="abs body-text" style="left:55px;top:784px;width:103px;text-align:justify">Lorem Ipsum is simply dummy text of the printing and typeset-ting industry. Lorem Ipsum has been the industry's standard</p>
<a class="abs more" style="left:116px;top:820px">Learn more</a>
<div class="abs news-date" style="top:858px">28<small>Feb</small></div>
<p class="abs body-text" style="left:55px;top:855px;width:103px;text-align:justify">Lorem Ipsum is simply dummy text of the printing and typeset-ting industry. Lorem Ipsum has been the industry's standard</p>
<a class="abs more" style="left:116px;top:891px">Learn more</a>
<div class="abs news-date" style="top:928px">28<small>Feb</small></div>
<p class="abs body-text" style="left:55px;top:925px;width:103px;text-align:justify">Lorem Ipsum is simply dummy text of the printing and typeset-ting industry. Lorem Ipsum has been the industry's standard</p>
<a class="abs more" style="left:116px;top:961px">Learn more</a>
<div class="abs" style="left:182px;top:785px;height:183px;border-left:1px dotted #777"></div>

<h3 class="abs section-title" style="left:208px;top:763px;color:var(--green-mid)">Testimonials</h3>
<div class="abs" style="left:308px;top:760px;width:22px;height:18px;background:#eeeae2;border:1px solid #aaa;transform:rotate(-6deg)"></div>
<p class="abs body-text" style="left:208px;top:784px;width:148px;text-align:justify">Lorem Ipsum is simply dummy text of the printing and typesetting industry. Lorem Ipsum has been the industry's standard dummy text ever since the 1500s, when an</p>
<em class="abs body-text" style="left:320px;top:820px">Mr Dalton</em>
<div class="abs" style="left:208px;top:835px;width:148px;border-top:1px dotted #777"></div>
<p class="abs body-text" style="left:208px;top:855px;width:148px;text-align:justify">Lorem Ipsum is simply dummy text of the printing and typesetting industry. Lorem Ipsum has been the industry's standard dummy text ever since the 1500s, when an</p>
<em class="abs body-text" style="left:320px;top:891px">Mr Dalton</em>
<div class="abs" style="left:208px;top:906px;width:148px;border-top:1px dotted #777"></div>
<p class="abs body-text" style="left:208px;top:926px;width:148px;text-align:justify">Lorem Ipsum is simply dummy text of the printing and typesetting industry. Lorem Ipsum has been the industry's standard dummy text ever since the 1500s, when an</p>
<em class="abs body-text" style="left:320px;top:962px">Mr Dalton</em>

<form class="abs contact">
  <div class="abs" style="left:15px;top:5px;width:30px;height:14px;background:#cfc8b8;border-radius:2px"></div>
  <h3 class="abs section-title" style="left:60px;top:6px;color:var(--green-mid);font-weight:400">Contact Us</h3>
  <label style="top:41px">Name *</label><span class="field" style="top:36px"></span>
  <label style="top:64px">Last Name *</label><span class="field" style="top:60px"></span>
  <label style="top:89px">Email *</label><span class="field" style="top:85px"></span>
  <label style="top:113px">Comapny *</label><span class="field" style="top:109px"></span>
  <label style="top:136px">Message *</label><span class="field" style="top:133px;height:45px"></span>
  <a class="abs btn btn-dark" style="left:163px;top:187px;width:62px;height:13px;line-height:13px">Learn more</a>
</form>

<div class="abs" style="left:0;top:998px;width:690px;border-top:1px solid var(--line)"></div>
<a class="abs" style="left:270px;top:989px;width:147px;height:20px;border:1px solid var(--line);border-radius:10px;background:var(--beige-light);font-size:7px;line-height:18px;padding-left:44px;color:var(--ink)"><span class="abs" style="left:12px;top:3px;width:16px;height:12px;background:#b9bdb8;border-radius:2px"></span>NEWSLETTER SIGN UP</a>

<footer class="abs footer">
  <h4 style="left:9px">QUICK LINKS</h4>
  <ul style="left:9px"><li>Home</li><li>About us</li><li>Services</li><li>Associate</li><li>Our &nbsp;mission</li><li>Contact us</li><li>Privacy policy</li><li>Terms of use</li><li>Site map</li></ul>
  <h4 style="left:183px">SERVICES</h4>
  <ul style="left:183px"><li>Services 1</li><li>Services 2</li><li>Services 3</li><li>Services 4</li><li>Services5</li><li>Services6</li><li>Services7</li></ul>
  <h4 style="left:356px">CONTACT US</h4>
  <p class="abs" style="left:356px;top:36px;font-size:10px">Address :</p>
  <p class="abs" style="left:356px;top:50px;font-size:7px">Comapny Address Goes Herea:</p>
  <p class="abs" style="left:356px;top:110px;font-size:7px;line-height:10px">Phone : 303-602-3381<br>Email : info@velmorhold.example</p>
  <h4 style="left:528px">SOCIAL MEDIA LINKS</h4>
  <span class="abs" style="left:528px;top:30px;width:30px;height:22px;border-radius:50%;background:#d8cdb4"></span>
  <span class="abs" style="left:568px;top:30px;width:30px;height:22px;border-radius:50%;background:#d8cdb4"></span>
  <span class="abs" style="left:609px;top:30px;width:30px;height:22px;border-radius:50%;background:#d8cdb4"></span>
  <span class="abs" style="left:528px;top:76px;width:32px;height:20px;border-radius:50%;background:#d8cdb4"></span>
  <p class="abs" style="left:566px;top:73px;font-size:12px;line-height:12px">Velmor Holdings<br><span style="font-size:9px">Financial Consultant</span></p>
</footer>
<div class="abs copyright">All Copyright reserved by comapny name</div>

</body>
</html>
```